AI Business Tools Landing Page

My web-based website builder (Pavlora.com) will be adding many new features in the very near future and I need an eye-catching landing page to promote these new products.

The page will have a primary section of the 8 main products we are promoting:
1. AI Instant Website Generator
2. AI Chatbot
3. Online Store Builder with AI Assistance
4. AI Auto-Blogging System
5. Online Scheduling System
6. Custom Email System
7. SEO Service
8. CRM System

The page will also have a smaller section for links to our affiliate programs. These can be smaller, less-promanent buttons or links. These are the affiliate products:
1. Get Your LLC
2. Website Design and Maintenance
3. Search Ads Management
4. Social Media Posting Service
5. Logo Design
6. Trademark Registration
7. Patent Application
8. Printing Services (including postcards, flyers, and merch.)
9. Bulk AI Content Generator

The theme and color scheme of the page should follow the theme of our main website, which is https://pavlora.com.

I need the page fully coded and ready to deploy on my server.

I look forward to seeing your amazing designs!

```html
<!DOCTYPE html>
<html lang="en">
<head>
<meta charset="utf-8">
<title>Pavlora – AI Business Tools</title>
<link href="https://fonts.googleapis.com/css2?family=Poppins:wght@400;500;600;700&family=Lato:wght@400&display=swap" rel="stylesheet">
<style>
  :root{
    --navy:#0b2440;
    --navy-deep:#08203a;
    --sky:#4fb7e5;
    --cyan:#35b6e6;
    --blue:#1e6fd0;
    --bright-blue:#0a78e0;
    --ink:#111722;
    --muted:#555b63;
    --line:#d9dde3;
    --panel:#f3f3f6;
    --white:#ffffff;
  }
  *{box-sizing:border-box;margin:0;padding:0}
  html,body{width:829px;height:1200px;overflow:hidden;background:var(--white)}
  body{position:relative;font-family:"Poppins",sans-serif;color:var(--ink)}

  .site-header{height:59px;background:var(--navy);display:flex;align-items:center;justify-content:center}
  .brand{display:flex;align-items:center;gap:8px;color:var(--white);font-family:"Poppins",sans-serif;font-weight:500;font-size:21px;letter-spacing:.2px}
  .brand-dot{width:20px;height:20px;border-radius:50%;background:var(--cyan)}

  .section-title{text-align:center;font-weight:700;color:var(--navy);letter-spacing:.2px}
  .divider{position:absolute;left:0;width:829px;display:flex;justify-content:center;align-items:center;gap:10px}
  .divider span{display:block;height:2px;background:var(--sky)}
  .divider i{display:block;width:12px;height:12px;border-radius:50%;background:var(--sky)}

  .tools-title{position:absolute;top:91px;width:829px;font-size:22.5px}
  .tools-divider{top:132px}
  .tools-divider span{width:48px}

  .tool-grid{position:absolute;left:35.5px;top:173.5px;width:758px;display:grid;grid-template-columns:repeat(4,176px);column-gap:18.6px;row-gap:41.5px}
  .tool-card{height:234px;background:var(--white);box-shadow:0 1px 6px rgba(0,0,0,.14);display:flex;flex-direction:column;position:relative}
  .tool-card.tall{height:241.5px}
  .tool-photo{height:127px;position:relative;overflow:hidden}
  .tool-photo svg{position:absolute;left:0;bottom:-1px;width:100%;height:16px}
  .tool-name{flex:1;display:flex;align-items:center;justify-content:center;text-align:center;font-weight:500;font-size:15.3px;line-height:17.5px;padding:0 8px}
  .tool-btn{height:23.7px;background:var(--navy);color:var(--white);font-size:8.8px;font-weight:700;text-transform:uppercase;display:flex;align-items:center;justify-content:center;text-decoration:none;letter-spacing:.1px}
  .tool-card.is-active .tool-name{color:var(--sky)}
  .tool-card.is-active .tool-btn{background:var(--sky)}
  .tool-badge{position:absolute;left:69px;top:102px;width:39px;height:39px;border-radius:50%;background:var(--sky);display:flex;align-items:center;justify-content:center;z-index:2}

  .p1{background:linear-gradient(135deg,#0d2a55,#1a4f8f 55%,#0a1c36)}
  .p2{background:linear-gradient(160deg,#0f5a7a,#1c8fb0 50%,#0a2d45)}
  .p3{background:linear-gradient(135deg,#2a4a6a,#6c8aa6 50%,#1a2d44)}
  .p4{background:linear-gradient(135deg,#3a3f45,#8a8f80 45%,#b5532a 80%,#2a2f33)}
  .p5{background:linear-gradient(135deg,#0a1426,#23345a 50%,#d5d8dc 95%)}
  .p6{background:linear-gradient(135deg,#3a3330,#5f6f7a 45%,#9a7a55 90%)}
  .p7{background:radial-gradient(circle at 50% 45%,#4fb0e8,#15406e 55%,#0a1e3a)}
  .p8{background:linear-gradient(135deg,#1d2a3c,#4f7ea8 45%,#d99a4a 100%)}

  .affiliates{position:absolute;left:0;top:749px;width:829px;height:392px;background:linear-gradient(180deg,#f2eef6 0%,var(--panel) 40%,var(--panel) 100%)}
  .aff-title{position:absolute;top:32px;width:829px;font-size:23.5px}
  .aff-divider{top:68.5px}
  .aff-divider span{width:63px}
  .aff-grid{position:absolute;left:35.5px;top:110.6px;display:grid;grid-template-columns:236px 236px 236px;column-gap:21.5px;row-gap:24px}
  .aff-grid .aff-link:nth-child(3n+2){margin-left:4px}
  .aff-grid .aff-link:nth-child(3n){margin-left:0;position:relative;left:0}
  .aff-link{height:57px;background:var(--white);border:1px solid var(--line);box-shadow:0 1px 3px rgba(0,0,0,.06);display:flex;align-items:center;text-decoration:none;color:var(--muted);font-size:15.2px;line-height:20.5px;padding-left:30.5px}
  .aff-icon{width:39px;height:39px;border-radius:50%;background:var(--cyan);display:flex;align-items:center;justify-content:center;flex:none;margin-right:24px}
  .aff-icon.deep{background:var(--blue)}
  .aff-link.is-active{background:var(--bright-blue);border-color:var(--bright-blue);color:var(--white)}
  .aff-link.is-active .aff-icon{background:var(--white)}

  .site-footer{position:absolute;left:0;top:1141px;width:829px;height:59px;background:var(--navy-deep)}
  .site-footer .brand{position:absolute;left:40px;top:17px;font-size:20.7px}
  .copyright{position:absolute;left:0;width:829px;top:1160px;text-align:center;font-family:"Lato",sans-serif;font-size:10px;color:var(--white)}
</style>
</head>
<body>

<header class="site-header">
  <div class="brand"><span class="brand-dot"></span>Pavlora</div>
</header>

<h1 class="section-title tools-title">AI Business Tools</h1>
<div class="divider tools-divider"><span></span><i></i><span></span></div>

<main class="tool-grid">
  <article class="tool-card">
    <div class="tool-photo p1" role="img" aria-label="Hand at a laptop holding a glowing AI hologram">
      <svg viewBox="0 0 176 16" preserveAspectRatio="none"><path d="M0 6 C50 -2 110 -2 176 10 L176 16 L0 16Z" fill="#fff"/></svg>
    </div>
    <h2 class="tool-name">AI Instant Website Generator</h2>
    <a class="tool-btn" href="#">Learn more</a>
  </article>
  <article class="tool-card">
    <div class="tool-photo p2" role="img" aria-label="Small robot on a glowing circuit board">
      <svg viewBox="0 0 176 16" preserveAspectRatio="none"><path d="M0 6 C50 -2 110 -2 176 10 L176 16 L0 16Z" fill="#fff"/></svg>
    </div>
    <h2 class="tool-name">AI ChatBot</h2>
    <a class="tool-btn" href="#">Learn more</a>
  </article>
  <article class="tool-card">
    <div class="tool-photo p3" role="img" aria-label="Finger touching floating SEO icons above a laptop">
      <svg viewBox="0 0 176 16" preserveAspectRatio="none"><path d="M0 6 C50 -2 110 -2 176 10 L176 16 L0 16Z" fill="#fff"/></svg>
    </div>
    <h2 class="tool-name">SEO Service</h2>
    <a class="tool-btn" href="#">Learn more</a>
  </article>
  <article class="tool-card">
    <div class="tool-photo p4" role="img" aria-label="Robot picking produce from store shelves">
      <svg viewBox="0 0 176 16" preserveAspectRatio="none"><path d="M0 6 C50 -2 110 -2 176 10 L176 16 L0 16Z" fill="#fff"/></svg>
    </div>
    <h2 class="tool-name">Online Store Builder with AI Assistance</h2>
    <a class="tool-btn" href="#">Learn more</a>
  </article>

  <article class="tool-card tall">
    <div class="tool-photo p5" role="img" aria-label="Robot arm working on an AI dashboard">
      <svg viewBox="0 0 176 16" preserveAspectRatio="none"><path d="M0 6 C50 -2 110 -2 176 10 L176 16 L0 16Z" fill="#fff"/></svg>
    </div>
    <h2 class="tool-name">AI Auto-Blogging System</h2>
    <a class="tool-btn" href="#">Learn more</a>
  </article>
  <article class="tool-card tall is-active">
    <div class="tool-photo p6" role="img" aria-label="Robot beside a laptop with floating calendar screens">
      <svg viewBox="0 0 176 16" preserveAspectRatio="none"><path d="M0 6 C50 -2 110 -2 176 10 L176 16 L0 16Z" fill="#fff"/></svg>
    </div>
    <div class="tool-badge">
      <svg width="20" height="20" viewBox="0 0 20 20" fill="none" stroke="#fff" stroke-width="1.4"><rect x="2" y="3" width="16" height="11" rx="1"/><path d="M7 17h6M10 14v3M5 7h5M5 10h3"/><rect x="12" y="6" width="4" height="4"/></svg>
    </div>
    <h2 class="tool-name">Online Scheduling System</h2>
    <a class="tool-btn" href="#">Learn more</a>
  </article>
  <article class="tool-card tall">
    <div class="tool-photo p7" role="img" aria-label="Hands holding a glowing network of customer contacts">
      <svg viewBox="0 0 176 16" preserveAspectRatio="none"><path d="M0 6 C50 -2 110 -2 176 10 L176 16 L0 16Z" fill="#fff"/></svg>
    </div>
    <h2 class="tool-name">CRM System</h2>
    <a class="tool-btn" href="#">Learn more</a>
  </article>
  <article class="tool-card tall">
    <div class="tool-photo p8" role="img" aria-label="Hands typing on a laptop with floating email windows">
      <svg viewBox="0 0 176 16" preserveAspectRatio="none"><path d="M0 6 C50 -2 110 -2 176 10 L176 16 L0 16Z" fill="#fff"/></svg>
    </div>
    <h2 class="tool-name">Custom emails using your domain</h2>
    <a class="tool-btn" href="#">Learn more</a>
  </article>
</main>

<section class="affiliates">
  <h2 class="section-title aff-title">Affiliate Programs</h2>
  <div class="divider aff-divider"><span></span><i></i><span></span></div>

  <nav class="aff-grid">
    <a class="aff-link" href="#"><span class="aff-icon"><svg width="20" height="20" viewBox="0 0 20 20" fill="none" stroke="#fff" stroke-width="1.3"><path d="M3 18V3h8v15M11 8h6v10M2 18h16M5 6h1M8 6h1M5 9h1M8 9h1M5 12h1M8 12h1M13 11h2M13 14h2"/></svg></span>Get Your LLC</a>
    <a class="aff-link" href="#"><span class="aff-icon deep"><svg width="20" height="20" viewBox="0 0 20 20" fill="none" stroke="#fff" stroke-width="1.3"><rect x="2" y="3" width="13" height="11" rx="1"/><path d="M2 6h13M5 9h5M5 11h3"/><circle cx="15" cy="14" r="3"/><path d="M15 10.5v1M15 16.5v1M11.5 14h1M17.5 14h1"/></svg></span>Website Design and Maintenance</a>
    <a class="aff-link" href="#"><span class="aff-icon"><svg width="20" height="20" viewBox="0 0 20 20" fill="none" stroke="#fff" stroke-width="1.3"><rect x="2.5" y="4" width="15" height="12" rx="3"/><text x="10" y="13" text-anchor="middle" font-family="Poppins,sans-serif" font-size="6.5" font-weight="700" fill="#fff" stroke="none">TM</text></svg></span>Trademark Registration</a>

    <a class="aff-link" href="#"><span class="aff-icon"><svg width="20" height="20" viewBox="0 0 20 20" fill="none" stroke="#fff" stroke-width="1.3"><rect x="3" y="3" width="14" height="14"/><path d="M6.5 15L10 5l3.5 10M8 11h4"/></svg></span>Logo Design</a>
    <a class="aff-link is-active" href="#"><span class="aff-icon"><svg width="20" height="20" viewBox="0 0 20 20" fill="none" stroke="#0a78e0" stroke-width="1.3"><rect x="2" y="3" width="16" height="12" rx="1"/><path d="M6 8h2l5-3v8l-5-3H6zM7 10l1 3"/></svg></span>Search Ads Management</a>
    <a class="aff-link" href="#"><span class="aff-icon"><svg width="20" height="20" viewBox="0 0 20 20" fill="none" stroke="#fff" stroke-width="1.3"><path d="M5 17v-3a6 6 0 1 1 8 0v3"/><circle cx="9" cy="9" r="2"/><path d="M9 5v1M9 12v1M5 9h1M12 9h1"/></svg></span>AI Content Generator</a>

    <a class="aff-link" href="#"><span class="aff-icon"><svg width="20" height="20" viewBox="0 0 20 20" fill="none" stroke="#fff" stroke-width="1.3"><path d="M5 8a5 5 0 0 1 10 0"/><rect x="3" y="8" width="14" height="6" rx="1"/><rect x="6" y="12" width="8" height="5"/></svg></span>Printing Services</a>
    <a class="aff-link" href="#"><span class="aff-icon deep"><svg width="20" height="20" viewBox="0 0 20 20" fill="none" stroke="#fff" stroke-width="1.3"><circle cx="6" cy="6" r="2.2"/><circle cx="14" cy="6" r="2.2"/><circle cx="10" cy="14" r="2.2"/><path d="M7.5 7.5l1.5 4.5M12.5 7.5L11 12M8.2 6h3.6"/></svg></span>Social Media Posting Service</a>
    <a class="aff-link" href="#"><span class="aff-icon"><svg width="20" height="20" viewBox="0 0 20 20" fill="none" stroke="#fff" stroke-width="1.3"><rect x="4" y="3" width="10" height="14" rx="1"/><path d="M7 3V2h4v1M6.5 7h5M6.5 10h5M6.5 13h2"/><circle cx="14" cy="14" r="2.5"/></svg></span>Patent Application</a>
  </nav>
</section>

<footer class="site-footer">
  <div class="brand"><span class="brand-dot"></span>Pavlora</div>
</footer>
<p class="copyright">© 2024 Pavlora. All Rights Reserved</p>

</body>
</html>
```